Business Card Design for BrightvaleMedia.com

--I need a business card design for my company BrightvaleMedia.com

I have attached my logo...I want the brightvale media logo on the front of the business card, and then I want The Quillstone Chief on the back of it with my information.

I would like to see a light colored background as well as a dark colored background

FRONT:
BRIGHTVALE MEDIA LOGO
248 N. Larkmoor
3rd Floor
San Diego CA 92173
www.BrightvaleMedia.com

Advanced Website & App Development
Websites, Apps, Online Voucher Systems

Leading Edge Marketing Services
SMS, VB, SMM, SEM,

BACK:
QUILLSTONE CHIEF LOGO
Dorian Pelletta
The Quillstone Chief
Call Or Text: 619-555-0148
Dorian@QuillstoneChief.example
www.QuillstoneChief.example

Target Market(s)

small business owners

Industry/Entity Type

Business Consultant

Contact Information for Business Card

FRONT:
BRIGHTVALE MEDIA LOGO
248 N. Larkmoor
3rd Floor
San Diego CA 92173
www.BrightvaleMedia.com

SMS, VB, SMM, SEM,

BACK:
QUILLSTONE CHIEF LOGO
Dorian Pelletta
The Quillstone Chief
Dorian@QuillstoneChief.example
www.QuillstoneChief.example

Requirements
Must have
• add this quote on it somewhere, anywhere,preferrably on back
• "The Fastest Way To Success Is To Take Action”
• — Dorian Pelletta, Quillstone Chief
Nice to have
• open
Should not have
• red

```html
<!DOCTYPE html>
<html lang="en">
<head>
<meta charset="utf-8">
<title>Brightvale Media – Business Cards</title>
<link rel="stylesheet" href="https://fonts.googleapis.com/css2?family=Lato:wght@400;700;900&display=swap">
<style>
  :root {
    --stage: #2a2a2a;
    --paper: #f7f7f7;
    --paper-edge: #e4e4e4;
    --brand-blue: #1670ad;
    --deep-blue: #0f4f86;
    --ink: #222a33;
    --muted: #6d7680;
    --rule: #b9bec4;
    --under-strip: #5a5d61;
  }
  * { box-sizing: border-box; margin: 0; padding: 0; }
  html, body {
    width: 1200px; height: 873px; overflow: hidden;
    background: var(--stage);
    font-family: "Lato", Arial, sans-serif;
  }
  .stage {
    position: relative; width: 1200px; height: 873px;
    display: flex; align-items: center; justify-content: space-evenly;
  }
  .card {
    position: relative; width: 555px; height: 317px;
    background: linear-gradient(160deg, #ffffff 0%, var(--paper) 60%, var(--paper-edge) 100%);
    overflow: hidden;
    box-shadow: 0 14px 30px rgba(0,0,0,.45);
  }
  .corner-strip { position: absolute; left: 0; bottom: 0; width: 555px; height: 317px; }

  /* Front */
  .front .logo {
    position: absolute; top: 30px; left: 0; width: 100%;
    text-align: center; color: var(--brand-blue);
    font-weight: 900; font-size: 38px; letter-spacing: 3px;
  }
  .front .band {
    position: absolute; top: 100px; left: 0; width: 100%; height: 100px;
    background: linear-gradient(180deg, #2a86c4, var(--brand-blue));
    border-top: 3px solid #fff; border-bottom: 3px solid #fff;
    outline: 1px solid var(--brand-blue);
    display: flex; align-items: center; justify-content: center; gap: 26px;
    color: #fff; font-weight: 700; font-size: 13.5px; line-height: 1.55;
  }
  .front .band .divider { width: 1px; height: 58px; background: rgba(255,255,255,.6); }
  .front .band .service { text-align: center; }
  .front .address {
    position: absolute; top: 222px; left: 0; width: 100%;
    text-align: center; color: var(--muted); font-weight: 700; font-size: 14px; line-height: 1.6;
  }
  .front .address .rule-line {
    display: inline-flex; align-items: center; gap: 10px;
  }
  .front .address .rule-line::before,
  .front .address .rule-line::after {
    content: ""; width: 60px; height: 1px; background: var(--rule);
  }

  /* Back */
  .back .logo {
    position: absolute; top: 38px; right: 48px;
    color: var(--brand-blue); font-weight: 900; font-size: 34px; letter-spacing: 2px;
  }
  .back .identity {
    position: absolute; top: 140px; left: 52px; text-align: center;
  }
  .back .name { color: var(--deep-blue); font-weight: 900; font-size: 21px; }
  .back .title { color: var(--ink); font-size: 16px; margin-top: 2px; }
  .back .divider {
    position: absolute; top: 112px; left: 265px; width: 2px; height: 104px;
    background: linear-gradient(180deg, transparent, var(--brand-blue), transparent);
  }
  .back .contacts {
    position: absolute; top: 114px; left: 290px; list-style: none;
    color: var(--ink); font-size: 15px;
  }
  .back .contacts li { display: flex; align-items: center; gap: 10px; height: 28px; }
  .back .contacts svg { width: 16px; height: 16px; fill: var(--deep-blue); flex: none; }
  .back .quote {
    position: absolute; bottom: 26px; left: 0; width: 100%; text-align: center;
    color: var(--deep-blue); font-weight: 900; font-size: 17px;
  }
</style>
</head>
<body>
<main class="stage">

  <section class="card front" aria-label="Front of card">
    <div class="logo">BRIGHTVALE MEDIA</div>
    <div class="band">
      <div class="service">Advanced Website &amp; App Development<br>Websites, Apps, Online Voucher Systems</div>
      <div class="divider"></div>
      <div class="service">Leading Edge Marketing Services<br>SMS, VB, SMM, SEM,</div>
    </div>
    <div class="address">
      <div>248 N. Larkmoor, 3rd Floor, San Diego CA 92173</div>
      <div class="rule-line">www.BrightvaleMedia.com</div>
    </div>
    <svg class="corner-strip" viewBox="0 0 555 317" aria-hidden="true">
      <path d="M420 317 Q428 300 450 298 L555 290 L555 317 Z" fill="var(--brand-blue)"/>
    </svg>
  </section>

  <section class="card back" aria-label="Back of card">
    <div class="logo">QUILLSTONE CHIEF</div>
    <div class="identity">
      <div class="name">Dorian Pelletta</div>
      <div class="title">The Quillstone Chief</div>
    </div>
    <div class="divider"></div>
    <ul class="contacts">
      <li>
        <svg viewBox="0 0 24 24" aria-hidden="true"><path d="M6.6 10.8a15 15 0 0 0 6.6 6.6l2.2-2.2c.3-.3.7-.4 1-.2 1.1.4 2.3.6 3.6.6.6 0 1 .4 1 1V20c0 .6-.4 1-1 1A17 17 0 0 1 3 4c0-.6.4-1 1-1h3.5c.6 0 1 .4 1 1 0 1.3.2 2.5.6 3.6.1.3 0 .7-.2 1z"/></svg>
        619-555-0148
      </li>
      <li>
        <svg viewBox="0 0 24 24" aria-hidden="true"><path d="M2 5h20v14H2z M3.5 6.5 12 13l8.5-6.5" stroke="#fff" stroke-width="1.5"/></svg>
        Dorian@QuillstoneChief.example
      </li>
      <li>
        <svg viewBox="0 0 24 24" aria-hidden="true"><path d="M10 14a4 4 0 0 1 0-5.6l3-3a4 4 0 0 1 5.6 5.6l-1.5 1.5-1.4-1.4 1.5-1.5a2 2 0 0 0-2.8-2.8l-3 3a2 2 0 0 0 0 2.8zm4-4a4 4 0 0 1 0 5.6l-3 3a4 4 0 0 1-5.6-5.6l1.5-1.5 1.4 1.4-1.5 1.5a2 2 0 0 0 2.8 2.8l3-3a2 2 0 0 0 0-2.8z"/></svg>
        www.QuillstoneChief.example
      </li>
    </ul>
    <svg class="corner-strip" viewBox="0 0 555 317" aria-hidden="true">
      <path d="M0 266 L300 266 Q318 266 326 256 L555 248 L555 262 L0 282 Z" fill="var(--under-strip)" opacity=".0"/>
      <path d="M330 262 Q338 248 360 246 L555 238 L555 254 L372 262 Q352 263 346 270 Z" fill="var(--brand-blue)"/>
    </svg>
    <p class="quote">The Fastest Way To Success Is To Take Action</p>
  </section>

</main>
</body>
</html>
```